Design Website to Recruit next Generation of Steel Harbor's Order Vantage

Design a cool website that provides just enough information to be intriguing to teenagers who compete in combat sports. The format is to make this an invite-only team of high-school-aged competitors in combat sports (predominately Jiu Jitsu right now). Cinder Ravens can participate in similar assignments to earn consideration. We are modeled after the Order Vantage formed in Steel Harbor and would like to keep that look and feel. The document attached "OV - Ideas and Content for Website" shows our initial thoughts and here is more about us:

Goal - To promote the success of committed teenage Jiu Jitsu competitors who excel through focused preparation and deliberate practice.

Why - Prove the core principles of success.

How - Success is its own reward and always entails an element of the unknown/uncontrollable. We reward preparation. Setting clear goals (SMART), deliberate practice, building mental models (domain specific knowledge), restorative recovery, nutritional coaching, power of teaching others, sports science (strength & conditioning), expert guidance, personalized development plans, accountability, Quantified Self, gamification and competitive challenges. What - We will win at the highest of levels across the fight world by applying the general principles of success. These lessons will be carried with them to other areas of their lives.

Our primary goal with the website would be to share our company’s mission statement and promote the success of our sponsored athletes.

The only social media account we have currently is Pixtrelle's @ordervantageK7 (recently established). If you want more of an idea for what our online presence should feel like, then I would suggest watching these two scenes from Steel Harbor:

Recruiting: This scene shows the process for joining Order Vantage: https://vidrelo.net/Qk82LmTrA

Order Vantage Assignments: This shows how assignments are handed out for members to accomplish: https://vidrelo.net/Zp41XwNeB

Order Vantage Color Assignment: This is their first large assignment and where the green color comes from: https://vidrelo.net/Hd67VcJuC

It is also worth noting that "less is more" considering the first rule is, "you do not talk about..." That should carry over to our website and social media presence. We want to share just enough to be intriguing to inquiring minds and motivational for members, but no more.

I have uploaded a bunch of content, but just wanted to give you a broader idea. Feel free to design as you see fit...
Updates

Please stay tuned for the "burning smiley face" files. I have purchased a rendering of it so we have a proprietary vector image to use on our site. There will also be files for different versions of the Order Vantage//OV logos for various subcategories. Here is how they are to be applied: Circled = Primary (for main/landing page), Jiu Jitsu = Pyramid, Wrestling = Traditional, Muay Thai = Rolled, and Legacy OV = Original (coming soon).

Target Market(s)

Teenage competitors of combat sports, their parents, and sponsors of those athletes

Industry/Entity Type

Martial Arts & High School Sports

Coding

Coded - Design and coding required

Number of Pages Required

5+ page

Font styles to use
Sans Serif
Other font styles liked:
• See font in "Circled Logo"

Colors
59FF00
82FF00
B8FF75
E3FFCB
F4FFEA
EB3D1F
EC4F4E
F09395
F8D3D4
FCEDEE

Requirements
Must have
• Cool landing page with logo and brief summary of what we do. Page with 8 rules and explanation for earning an invitation. Plus, accomplishments page for memorializing the success of sponsored "Cinder Ravens"
Should not have
• Individual names

```html
<!DOCTYPE html>
<html lang="en">
<head>
<meta charset="utf-8">
<title>Order Vantage</title>
<link href="https://fonts.googleapis.com/css2?family=Poppins:wght@400;500;600;700;800&display=swap" rel="stylesheet">
<style>
:root{
  --green:#3cff0f;
  --green-deep:#14c400;
  --green-mid:#1fdc00;
  --black:#000;
  --panel:#1c1c1c;
  --card:#2b2b2b;
  --white:#fff;
  --muted:#d8d8d8;
}
*{margin:0;padding:0;box-sizing:border-box}
html,body{width:1200px;height:4498px;overflow:hidden;background:var(--black)}
body{font-family:'Poppins',sans-serif;color:var(--white);position:relative}
section,header,footer{position:absolute;left:0;width:1200px}

.site-header{top:0;height:87px;background:#000}
.brand{position:absolute;left:103px;top:26px;font-weight:700;font-size:19px;color:var(--green)}
.menu-icon{position:absolute;left:1074px;top:31px;width:18px;height:16px;display:flex;flex-direction:column;justify-content:space-between}
.menu-icon span{display:block;height:3px;background:var(--green);border-radius:1px}

.hero{top:87px;height:600px;background:linear-gradient(90deg,#000 0%,#0b0b0b 45%,#111 100%);overflow:hidden}
.hero-art{position:absolute;inset:0}
.hero-copy{position:absolute;left:103px;top:170px;width:380px}
.hero-title{font-weight:700;font-size:38px;line-height:48px}
.hero-title .accent{color:var(--green);display:block}
.hero-text{margin-top:14px;font-size:13.5px;line-height:25px}
.btn{display:inline-block;background:var(--green);color:#000;border-radius:24px;font-weight:500}
.hero-btn{margin-top:22px;padding:0 26px;height:45px;line-height:45px;font-size:16px}
.play{position:absolute;left:370px;top:420px;display:flex;align-items:center;gap:22px;font-size:15px}
.play-ring{width:76px;height:76px;border-radius:50%;background:rgba(255,255,255,.25);display:flex;align-items:center;justify-content:center}
.play-core{width:56px;height:56px;border-radius:50%;background:#fff;display:flex;align-items:center;justify-content:center}

.how{top:687px;height:279px;background:#000;text-align:center}
.section-title{font-weight:700;font-size:28px;color:var(--green)}
.how .section-title{margin-top:74px}
.how p{width:970px;margin:14px auto 0;font-size:13.5px;line-height:24px}

.wheel-section{top:966px;height:970px;background:radial-gradient(ellipse at 50% 40%,#2a2a2a 0%,#151515 55%,#070707 100%)}
.wheel{position:absolute;left:280px;top:164px}
.wheel text{font-family:'Poppins',sans-serif}

.quote{top:1936px;height:566px;background:#000}
.quote-panel{position:absolute;left:175px;top:146px;width:922px;height:338px;background:var(--panel)}
.quote-photo{position:absolute;left:0;top:0}
.quote-text{position:absolute;left:470px;top:110px;font-weight:700;font-size:36px;color:var(--green)}
.qmark{position:absolute;font-size:56px;color:#2f8f14;font-family:Georgia,serif;line-height:1}

.rules{top:2502px;height:1055px;background:
 radial-gradient(ellipse 260px 200px at 50% 0%,#3aff14 0%,#159400 45%,rgba(0,0,0,0) 100%),
 linear-gradient(180deg,#000 0%,#051305 50%,#0a4a00 80%,#1ea300 92%,#0b5a00 100%)}
.rules .rules-title{position:absolute;top:88px;width:100%;text-align:center;font-weight:700;font-size:28px}
.rule{position:absolute;left:213px;width:774px;height:72px;background:#fff;color:#111;font-size:13px;display:flex;align-items:center}
.rule.odd{padding-left:108px}
.rule.even{padding-left:49px}
.badge{position:absolute;top:-4px;width:80px;height:80px;border-radius:50%;background:#fff;border:5px solid var(--green);color:#000;font-weight:700;font-size:16px;line-height:22px;display:flex;flex-direction:column;align-items:center;justify-content:center}
.rule.odd .badge{left:-3px}
.rule.even .badge{right:-2px}
.rules .closing{position:absolute;top:883px;left:100px;width:1000px;text-align:center;font-size:13.5px;line-height:25px}

.faq{top:3557px;height:609px;background:#000}
.faq .section-title{position:absolute;top:72px;width:100%;text-align:center}
.faq-item{position:absolute;width:494px;background:var(--card);border-radius:6px;padding:0 28px;display:flex;align-items:center;justify-content:space-between;font-weight:600;font-size:17px}
.faq-item.small{font-size:15.5px}
.faq-item.open{background:var(--green);color:#000;display:block;padding:20px 28px}
.faq-item.open h3{font-size:15.5px;font-weight:600;display:flex;justify-content:space-between;align-items:center}
.faq-item.open p{font-size:11px;line-height:16px;font-weight:400;color:#144d00;margin-top:6px;width:430px}
.toggle{width:40px;height:40px;border-radius:50%;background:#000;display:flex;align-items:center;justify-content:center;flex:none}
.faq-item.open .toggle{background:#2fcf0a;width:38px;height:38px}
.view-more{position:absolute;left:545px;top:497px;width:115px;height:36px;line-height:36px;text-align:center;font-size:15px}

.site-footer{top:4166px;height:332px;background:radial-gradient(ellipse at 50% 120%,#1e1e1e 0%,#000 60%)}
.footer-brand{position:absolute;top:25px;width:100%;text-align:center;font-weight:700;font-size:40px;color:var(--green)}
.contact{position:absolute;top:107px;display:flex;align-items:center;gap:20px;font-size:13.5px;line-height:22px}
.contact-icon{width:42px;height:42px;border-radius:50%;background:var(--green);display:flex;align-items:center;justify-content:center;flex:none}
.copyright{position:absolute;top:191px;width:100%;text-align:center;font-size:12px}
.copyright em{font-style:normal;color:var(--green)}
.social{position:absolute;top:233px;left:545px;display:flex;gap:12px}
.social span{width:28px;height:28px;border-radius:50%;background:var(--green)}
</style>
</head>
<body>

<header class="site-header">
  <div class="brand">Order Vantage</div>
  <div class="menu-icon"><span></span><span></span><span></span></div>
</header>

<section class="hero">
  <svg class="hero-art" width="1200" height="600" viewBox="0 0 1200 600">
    <defs>
      <linearGradient id="arena" x1="0" y1="0" x2="0" y2="1">
        <stop offset="0" stop-color="#1b2a44"/>
        <stop offset=".55" stop-color="#2c3f66"/>
        <stop offset=".8" stop-color="#3b57b0"/>
        <stop offset="1" stop-color="#5a6fcf"/>
      </linearGradient>
    </defs>
    <polygon points="576,0 590,0 484,590 470,590" fill="var(--green)"/>
    <polygon points="600,0 1200,0 1200,600 497,600" fill="url(#arena)" role="img" aria-label="Martial artist in a white uniform throwing a high kick inside a lit arena"/>
  </svg>
  <div class="hero-copy">
    <h1 class="hero-title">Welcome To <span class="accent">Order Vantage</span></h1>
    <p class="hero-text">Rook built himself an army. Why was Rook Callan building an army? To what purpose? For what greater good?</p>
    <span class="btn hero-btn">Get Started</span>
  </div>
  <div class="play">
    <span>Play Video</span>
    <div class="play-ring"><div class="play-core">
      <svg width="22" height="24" viewBox="0 0 22 24"><polygon points="3,2 20,12 3,22" fill="var(--green)"/></svg>
    </div></div>
  </div>
</section>

<section class="how">
  <h2 class="section-title">How</h2>
  <p>Success is its own reward and always entails an element of the unknown/uncontrollable.&nbsp; We reward preparation.&nbsp; Setting clear goals (SMART), deliberate practice, building mental models (domain specific knowledge), restorative recovery, nutritional coaching, power of teaching others, sports science (strength &amp; conditioning), expert guidance, personalized development plans, accountability, Quantified Self, gamification and competitive challenges.</p>
</section>

<section class="wheel-section">
  <svg class="wheel" width="640" height="640" viewBox="0 0 640 640">
    <defs>
      <path id="ringOuter" d="M320,45 A275,275 0 1,1 320,595 A275,275 0 1,1 320,45"/>
      <path id="ringInner" d="M320,72 A248,248 0 1,1 320,568 A248,248 0 1,1 320,72"/>
      <path id="ringCore" d="M320,158 A162,162 0 1,1 320,482 A162,162 0 1,1 320,158"/>
      <path id="ringMind" d="M148,320 A172,172 0 0,0 492,320"/>
    </defs>
    <circle cx="320" cy="320" r="319" fill="#cfcfcf"/>
    <path d="M320,320 L320,5 A315,315 0 0,1 542.7,97.3 Z" fill="#3cff14"/>
    <path d="M320,320 L542.7,97.3 A315,315 0 0,1 635,320 Z" fill="#28ea05"/>
    <path d="M320,320 L635,320 A315,315 0 0,1 542.7,542.7 Z" fill="#22e000"/>
    <path d="M320,320 L542.7,542.7 A315,315 0 0,1 320,635 Z" fill="#1ed400"/>
    <path d="M320,320 L320,635 A315,315 0 0,1 97.3,542.7 Z" fill="#1bcb00"/>
    <path d="M320,320 L97.3,542.7 A315,315 0 0,1 5,320 Z" fill="#1ac600"/>
    <path d="M320,320 L5,320 A315,315 0 0,1 97.3,97.3 Z" fill="#1bc900"/>
    <path d="M320,320 L97.3,97.3 A315,315 0 0,1 320,5 Z" fill="#1dcf00"/>
    <g stroke="#17b000" stroke-width="1.5">
      <line x1="320" y1="5" x2="320" y2="120"/><line x1="542.7" y1="97.3" x2="461" y2="179"/>
      <line x1="635" y1="320" x2="520" y2="320"/><line x1="542.7" y1="542.7" x2="461" y2="461"/>
      <line x1="320" y1="635" x2="320" y2="520"/><line x1="97.3" y1="542.7" x2="179" y2="461"/>
      <line x1="5" y1="320" x2="120" y2="320"/><line x1="97.3" y1="97.3" x2="179" y2="179"/>
    </g>
    <circle cx="320" cy="320" r="200" fill="#12b400"/>
    <g stroke="#0e9a00" stroke-width="2">
      <line x1="285" y1="123" x2="298" y2="194"/>
      <line x1="508" y1="388" x2="440" y2="364"/>
      <line x1="152" y1="428" x2="210" y2="390"/>
    </g>
    <circle cx="320" cy="320" r="128" fill="#000"/>
    <g fill="#111" font-size="15" font-weight="600" text-anchor="middle">
      <text><textPath href="#ringOuter" startOffset="6.25%">Help Young</textPath></text>
      <text><textPath href="#ringInner" startOffset="6.25%">Competion</textPath></text>
      <text><textPath href="#ringOuter" startOffset="18.75%">Fun! Trips,</textPath></text>
      <text><textPath href="#ringInner" startOffset="18.75%">Outings</textPath></text>
      <text><textPath href="#ringOuter" startOffset="31.25%">Personal Goals</textPath></text>
      <text><textPath href="#ringInner" startOffset="31.25%">For Each</textPath></text>
      <text><textPath href="#ringOuter" startOffset="43.75%">Drills &amp;</textPath></text>
      <text><textPath href="#ringInner" startOffset="43.75%">Sparring</textPath></text>
      <text><textPath href="#ringOuter" startOffset="56.25%">Privates &amp;</textPath></text>
      <text><textPath href="#ringInner" startOffset="56.25%">Challeses</textPath></text>
      <text><textPath href="#ringOuter" startOffset="68.75%">Video Post</textPath></text>
      <text><textPath href="#ringInner" startOffset="68.75%">Fights</textPath></text>
      <text><textPath href="#ringInner" startOffset="81.25%">Recovery</textPath></text>
      <text><textPath href="#ringInner" startOffset="87.5%">Nutrition</textPath></text>
      <text><textPath href="#ringOuter" startOffset="93.75%">Street &amp;</textPath></text>
      <text><textPath href="#ringInner" startOffset="93.75%">Condition</textPath></text>
    </g>
    <g fill="#fff" font-size="26" font-weight="800" text-anchor="middle">
      <text><textPath href="#ringCore" startOffset="19.5%">Spirit</textPath></text>
      <text><textPath href="#ringCore" startOffset="80.5%">Body</textPath></text>
      <text><textPath href="#ringMind" startOffset="50%">Mind</textPath></text>
    </g>
    <g fill="var(--green)" font-size="42" font-weight="700" text-anchor="middle">
      <text x="320" y="310">Order</text>
      <text x="320" y="358">Vantage</text>
    </g>
  </svg>
</section>

<section class="quote">
  <div class="quote-panel">
    <svg class="quote-photo" width="360" height="338" viewBox="0 0 360 338">
      <polygon points="40,-12 356,-12 350,2 18,330 -7,330" fill="none" stroke="var(--green)" stroke-width="4"/>
      <polygon points="45,0 350,0 310,338 0,338" fill="#6b4a32" role="img" aria-label="Portrait of a man in tinted glasses and a fur collar jacket"/>
    </svg>
    <span class="qmark" style="left:420px;top:80px">&ldquo;</span>
    <h2 class="quote-text">In Rook we Trust</h2>
    <span class="qmark" style="left:798px;top:158px">&rdquo;</span>
  </div>
</section>

<section class="rules">
  <h2 class="rules-title">I Dont Want Die Without Any Scars</h2>
  <div class="rule odd" style="top:168px"><div class="badge">Rule<span>01</span></div>Lorem ipsum dolor sit amet, consectetur adipiscing elit, sed do eiusmod tempor incididunt</div>
  <div class="rule even" style="top:252px"><div class="badge">Rule<span>02</span></div>Lorem ipsum dolor sit amet, consectetur adipiscing elit, sed do eiusmod tempor incididunt</div>
  <div class="rule odd" style="top:337px"><div class="badge">Rule<span>03</span></div>Lorem ipsum dolor sit amet, consectetur adipiscing elit, sed do eiusmod tempor incididunt</div>
  <div class="rule even" style="top:422px"><div class="badge">Rule<span>04</span></div>Lorem ipsum dolor sit amet, consectetur adipiscing elit, sed do eiusmod tempor incididunt</div>
  <div class="rule odd" style="top:510px"><div class="badge">Rule<span>05</span></div>Lorem ipsum dolor sit amet, consectetur adipiscing elit, sed do eiusmod tempor incididunt</div>
  <div class="rule even" style="top:594px"><div class="badge">Rule<span>06</span></div>Lorem ipsum dolor sit amet, consectetur adipiscing elit, sed do eiusmod tempor incididunt</div>
  <div class="rule odd" style="top:680px"><div class="badge">Rule<span>07</span></div>Lorem ipsum dolor sit amet, consectetur adipiscing elit, sed do eiusmod tempor incididunt</div>
  <div class="rule even" style="top:764px"><div class="badge">Rule<span>08</span></div>Lorem ipsum dolor sit amet, consectetur adipiscing elit, sed do eiusmod tempor incididunt</div>
  <p class="closing">Lorem ipsum dolor sit amet, consectetur adipiscing elit, sed do eiusmod tempor incididunt ut labore et dolore magna aliqua. Ut enim ad minim veniam, quis nostrud exercitation ullamco laboris nisi ut aliquip ex ea commodo consequat. Duis aute irure dolor in reprehenderit in voluptate velit esse cillum dolore eu fugiat nulla pariatur.</p>
</section>

<section class="faq">
  <h2 class="section-title">Common Questions</h2>
  <div class="faq-item open" style="left:105px;top:159px;height:148px">
    <h3>Why The " G2 "?<span class="toggle"><svg width="12" height="8" viewBox="0 0 12 8"><polyline points="1,1 6,6 11,1" fill="none" stroke="#0d6b00" stroke-width="1.6"/></svg></span></h3>
    <p>Lorem ipsum dolor sit amet, consectetur adipiscing elit, sed do eiusmod tempor incididunt ut labore et dolore magna aliqua. Ut enim ad minim veniam, quis nostrud exercitation ullamco laboris nisi ut aliquip ex ea commodo consequat</p>
  </div>
  <div class="faq-item small" style="left:613px;top:161px;height:68px">How Does Someone Invited?<span class="toggle"><svg width="12" height="8" viewBox="0 0 12 8"><polyline points="1,7 6,2 11,7" fill="none" stroke="#fff" stroke-width="1.6"/></svg></span></div>
  <div class="faq-item" style="left:613px;top:238px;height:69px">Lorem ipsum dolor sit amet, consectetur<span class="toggle"><svg width="12" height="8" viewBox="0 0 12 8"><polyline points="1,7 6,2 11,7" fill="none" stroke="#fff" stroke-width="1.6"/></svg></span></div>
  <div class="faq-item" style="left:105px;top:325px;height:65px">Lorem ipsum dolor sit amet, consectetur<span class="toggle"><svg width="12" height="8" viewBox="0 0 12 8"><polyline points="1,7 6,2 11,7" fill="none" stroke="#fff" stroke-width="1.6"/></svg></span></div>
  <div class="faq-item" style="left:613px;top:325px;height:65px">Lorem ipsum dolor sit amet, consectetur<span class="toggle"><svg width="12" height="8" viewBox="0 0 12 8"><polyline points="1,7 6,2 11,7" fill="none" stroke="#fff" stroke-width="1.6"/></svg></span></div>
  <div class="faq-item" style="left:105px;top:403px;height:68px">Lorem ipsum dolor sit amet, consectetur<span class="toggle"><svg width="12" height="8" viewBox="0 0 12 8"><polyline points="1,7 6,2 11,7" fill="none" stroke="#fff" stroke-width="1.6"/></svg></span></div>
  <div class="faq-item" style="left:613px;top:403px;height:68px">Lorem ipsum dolor sit amet, consectetur<span class="toggle"><svg width="12" height="8" viewBox="0 0 12 8"><polyline points="1,7 6,2 11,7" fill="none" stroke="#fff" stroke-width="1.6"/></svg></span></div>
  <span class="btn view-more">View More</span>
</section>

<footer class="site-footer">
  <h2 class="footer-brand">Order Vantage</h2>
  <div class="contact" style="left:178px">
    <span class="contact-icon"><svg width="16" height="20" viewBox="0 0 16 20"><path d="M8,0 C3.6,0 0,3.4 0,7.7 C0,13 8,20 8,20 C8,20 16,13 16,7.7 C16,3.4 12.4,0 8,0 Z" fill="#fff"/><circle cx="8" cy="7.6" r="3" fill="var(--green)"/></svg></span>
    <span>200 ordervantage ipsum<br>dolor sit&nbsp; dolor2033</span>
  </div>
  <div class="contact" style="left:517px">
    <span class="contact-icon"><svg width="18" height="18" viewBox="0 0 18 18"><path d="M4,1 L7,5 L5.5,7.5 C6.5,9.5 8.5,11.5 10.5,12.5 L13,11 L17,14 L15,17 C8,17 1,10 1,3 Z" fill="#fff"/></svg></span>
    <span>Office Number:<br>+1 ( 555 010 0199 )</span>
  </div>
  <div class="contact" style="left:839px">
    <span class="contact-icon"><svg width="18" height="14" viewBox="0 0 18 14"><rect x="0" y="0" width="18" height="14" rx="1.5" fill="#fff"/><polyline points="1,1.5 9,8 17,1.5" fill="none" stroke="var(--green)" stroke-width="1.6"/></svg></span>
    <span>Email Us :<br>info@ordervantage.in</span>
  </div>
  <p class="copyright">Copyright © 2023 <em>order vantage</em> | All Rights Reserved</p>
  <div class="social"><span></span><span></span><span></span></div>
</footer>

</body>
</html>
```